Tour operator needs simple coded WordPress site (updated extra payment for coding and guaranteed)

[update 9/7/2015]
If you design a new logo and it gets accepted, even if we use another template with your logo you will get $50
[update 8/7/2015]
Update on questions about dual-language
For dual languages we are happy to set up a second site with the same designs in a second language.
For the design aspect just allow the user to switch between languages with an icon.
For the coding, a replica of the site on a second server will do (to save messing around with multiple language plugins) - we will populate it with Chinese text
[original post]
Simple coded WordPress site for tours
You can choose to design only or design and code ($340 design, $150 bonus for coding)
Open design brief - use your creativity
Will be in 2 languages (English and Chinese) but design needs only to be in one language
Winning design will be chosen only from home page, but the winner must make a second standard template page when chosen at no extra cost.
Must be responsive design
We only need homepage and standard template page design and coding, we will populate the pages
You can use design ideas from our pamphlet if you like - attached
Only a sample logo and colors on website and pamphlet - feel free to change as the current ones seem restrictive
Current website framework only to give an idea of the number of pages and basic menu structure (no need to use existing navigation style or any style at all for that matter, open brief)
http://brightwattlejourneys.com.au/
Target Market(s)
Chinese parents of kids 10-14 (the kids will take the tour)
Industry/Entity Type
Tour
Number of Pages Required
2 page
Look and feel
Each slider illustrates characteristics of the customer's brand and the style your logo design should communicate.

```html
<!DOCTYPE html>
<html lang="en">
<head>
<meta charset="utf-8">
<title>Bright Wattle Journeys</title>
<link href="https://fonts.googleapis.com/css2?family=Open+Sans:wght@400;600;700;800&display=swap" rel="stylesheet">
<style>
:root{
  --orange:#f6a623;
  --orange-dark:#e08f0c;
  --navy:#27375f;
  --ink:#333;
  --muted:#777;
  --grey-band:#e9e9e9;
  --card:#fff;
  --footer:#1f1f1f;
  --footer-bar:#151515;
  --line:#d8d8d8;
}
*{box-sizing:border-box;margin:0;padding:0}
html,body{width:759px;height:1200px;overflow:hidden}
body{font-family:"Open Sans",Arial,sans-serif;color:var(--ink);background:#fff;position:relative;font-size:8px;line-height:1.45}
ul{list-style:none}

/* Hero */
.hero{position:absolute;left:0;top:0;width:759px;height:380px;background:linear-gradient(180deg,#1c2a44 0%,#2c3a58 35%,#6a5a4a 62%,#a8773c 78%,#3a3026 100%)}
.brand{position:absolute;left:70px;top:10px;display:flex;align-items:center;gap:8px}
.brand-mark{width:56px;height:56px;border-radius:50%;background:var(--navy);border:3px solid #fff}
.brand-name{font-weight:700;font-size:12px;color:#fff;letter-spacing:.5px}
.lang{position:absolute;right:70px;top:14px;width:62px;height:16px;background:#fff;border-radius:2px;font-size:8px;padding:1px 6px;color:var(--ink)}
.lang:after{content:"";position:absolute;right:6px;top:6px;border:3px solid transparent;border-top-color:#555}
.hero-title{position:absolute;right:70px;top:296px;width:440px;text-align:right;color:#fff;font-weight:800;font-size:15px;line-height:1.3;text-transform:uppercase;font-style:italic}
.social{position:absolute;right:70px;top:336px;display:flex;gap:8px}
.social span{width:18px;height:18px;border-radius:50%;border:1.5px solid #fff}
.nav{position:absolute;left:70px;top:356px;display:flex}
.nav a{display:block;width:112px;height:24px;background:#fff;color:var(--ink);text-decoration:none;font-size:8px;text-align:center;line-height:24px;border-right:1px solid #eee}
.nav a.active{border-bottom:2px solid var(--orange);font-weight:600}

/* Welcome */
.welcome{position:absolute;left:70px;top:408px;width:400px}
h2{font-size:13px;font-weight:700;color:var(--ink);text-transform:uppercase;margin-bottom:8px}
h2 em{font-style:normal;color:var(--orange)}
.welcome p{font-size:7.5px;color:#555;margin-bottom:6px}
.welcome p b{color:var(--ink)}
.btn{display:inline-block;background:var(--navy);color:#fff;font-weight:700;font-size:7.5px;padding:4px 14px;text-transform:uppercase}
.welcome .btn{position:absolute;right:0;top:150px}
.inquiry{position:absolute;left:494px;top:408px;width:195px}
.inquiry .field{border:1px solid var(--line);height:18px;margin-bottom:6px;font-size:7px;color:#999;padding:3px 5px}
.inquiry .field.msg{height:52px}
.inquiry .btn{float:right}

/* Features */
.features{position:absolute;left:0;top:618px;width:759px;height:222px;background:var(--grey-band)}
.cards{position:absolute;left:70px;top:16px;display:flex;gap:14px}
.card{width:197px;height:188px;background:var(--card);padding:12px 12px}
.card h3{font-size:8px;font-weight:700;text-transform:uppercase;color:var(--ink);display:flex;align-items:center;gap:6px;margin-bottom:8px;padding-bottom:6px;border-bottom:1px solid #eee}
.card h3 i{width:16px;height:16px;border-radius:50%;background:var(--orange);display:block}
.card li{font-size:6.8px;color:#555;padding-left:10px;position:relative;margin-bottom:3px}
.card li:before{content:"";position:absolute;left:0;top:2px;width:5px;height:3px;border-left:1.5px solid var(--orange);border-bottom:1.5px solid var(--orange);transform:rotate(-45deg)}
.card p{font-size:6.8px;color:#555;margin-bottom:4px}
.card p a{color:var(--orange)}

/* Includes */
.includes{position:absolute;left:0;top:840px;width:759px;height:150px;background:var(--orange)}
.includes h2{position:absolute;left:70px;top:14px;color:#fff;font-size:16px}
.inc-list{position:absolute;top:44px;width:160px}
.inc-list li{color:#fff;font-size:8px;font-weight:600;display:flex;align-items:center;gap:6px;margin-bottom:4px}
.inc-list li:before{content:"";width:9px;height:9px;border-radius:50%;background:#fff;opacity:.85}
.inc-list.left{left:70px}
.inc-list.right{left:300px}
.brochure{position:absolute;left:566px;top:44px;display:flex;gap:8px;align-items:flex-start}
.brochure svg{flex:none}
.brochure span{color:#fff;font-size:7.5px;font-weight:600;width:80px}

/* Footer */
.footer{position:absolute;left:0;top:990px;width:759px;height:186px;background:var(--footer);color:#ccc}
.footer h4{font-size:8.5px;font-weight:700;color:#fff;margin-bottom:8px;padding-bottom:5px;border-bottom:1px solid #3a3a3a}
.fcol{position:absolute;top:16px}
.quick{left:70px;width:110px}
.quick li{font-size:7px;margin-bottom:3px}
.quick li:before{content:"› ";color:var(--orange)}
.subscribe{left:220px;width:150px}
.subscribe p{font-size:7px;margin-bottom:8px}
.subscribe .field{height:14px;background:#fff;font-size:6.5px;color:#999;padding:2px 5px;width:110px;margin-bottom:6px}
.subscribe .btn{background:var(--orange);font-size:6.5px;padding:3px 10px}
.contact{left:404px;width:150px}
.contact li{font-size:7px;display:flex;gap:6px;align-items:flex-start;margin-bottom:7px}
.contact svg{flex:none;margin-top:1px}
.foot-brand{position:absolute;left:590px;top:22px;width:100px;text-align:center}
.foot-brand .brand-mark{width:70px;height:70px;margin:0 auto 6px;border-color:#ddd}
.foot-brand span{font-size:8px;font-weight:700;color:#fff}
.bottom{position:absolute;left:0;top:1176px;width:759px;height:24px;background:var(--footer-bar);color:#888;font-size:6.5px;text-align:center;line-height:24px}
</style>
</head>
<body>

<header class="hero" role="img" aria-label="Evening view of a harbour with a sail-roofed opera house and a steel arch bridge lit against the sky">
  <div class="brand"><span class="brand-mark"></span><span class="brand-name">Bright Wattle Journeys</span></div>
  <div class="lang">English</div>
  <p class="hero-title">Educational, safe, culturally Australian journeys — enlightening and fun.</p>
  <div class="social"><span></span><span></span><span></span></div>
  <nav class="nav">
    <a class="active" href="#">Home</a><a href="#">About Us</a><a href="#">Tours</a><a href="#">Contact Us</a>
  </nav>
</header>

<section class="welcome">
  <h2>Welcome to <em>Bright Wattle</em> Journeys</h2>
  <p><b>At Bright Wattle Journeys we are passionate about educational travel and opportunities for students to gain academic and cultural understanding of Australia.</b></p>
  <p>Our programs combine classroom visits, guided excursions and homestay experiences that open young minds to new people, places and ideas while building confidence in English.</p>
  <p>Every tour is planned by experienced educators so that students learn, explore and grow in a safe and caring setting. The rest of your questions are answered on our tours page.</p>
  <a class="btn" href="#">Read More</a>
</section>

<aside class="inquiry">
  <h2>Quick Inquiry</h2>
  <div class="field">Name</div>
  <div class="field">Email</div>
  <div class="field msg">Message</div>
  <a class="btn" href="#">Submit</a>
</aside>

<section class="features">
  <div class="cards">
    <article class="card">
      <h3><i></i>Educational and Cultural</h3>
      <ul>
        <li>Professional lecturers from leading universities</li>
        <li>Tutors help every child build confidence in spoken English</li>
        <li>Students meet local families and share daily life</li>
        <li>Visits to museums, galleries and national parks</li>
        <li>Hands-on workshops on local history and culture</li>
        <li>Outdoor activities and sport</li>
      </ul>
    </article>
    <article class="card">
      <h3><i></i>Safe and Secure</h3>
      <ul>
        <li>Staff hold approved checks for working with children</li>
        <li>Qualified supervisors travel with every group</li>
        <li>Accommodation chosen with student safety first</li>
        <li>Around-the-clock emergency contact line</li>
        <li>Parents receive daily updates and photos</li>
        <li>Small group sizes for close care</li>
      </ul>
    </article>
    <article class="card">
      <h3><i></i>Travel Insurance</h3>
      <p>Every student is covered by comprehensive travel insurance for the full length of the tour.</p>
      <p>The policy includes medical care, lost luggage and trip changes, arranged by <a href="#">brightwattlejourneys.com.au</a>.</p>
      <p>Please read the full policy before you book so you know exactly what is included.</p>
    </article>
  </div>
</section>

<section class="includes">
  <h2>Includes</h2>
  <ul class="inc-list left">
    <li>Return tickets</li>
    <li>Visa fees</li>
    <li>Travel accident insurance</li>
    <li>Accommodation</li>
    <li>Meals (breakfast, lunch and dinner)</li>
  </ul>
  <ul class="inc-list right">
    <li>Transportation</li>
    <li>Cinemas and concerts</li>
    <li>Studies</li>
    <li>Extra activities and travel equipment</li>
  </ul>
  <div class="brochure">
    <svg width="30" height="36" viewBox="0 0 30 36" aria-hidden="true"><path d="M2 1h18l8 8v26H2z" fill="#fff"/><path d="M20 1v8h8" fill="#ddd"/><rect x="2" y="20" width="26" height="9" fill="#c0392b"/></svg>
    <span>Download the Brochure (PDF)</span>
  </div>
</section>

<footer class="footer">
  <div class="fcol quick">
    <h4>Quick Links</h4>
    <ul><li>Home</li><li>About Us</li><li>Tours</li><li>Contact Us</li></ul>
  </div>
  <div class="fcol subscribe">
    <h4>Subscribe To Newsletter</h4>
    <p>Get latest updates by entering your email address</p>
    <div class="field">Email Address</div>
    <a class="btn" href="#">Subscribe</a>
  </div>
  <div class="fcol contact">
    <h4>Contact Detail</h4>
    <ul>
      <li><svg width="8" height="10" viewBox="0 0 8 10"><path d="M4 0a3.5 3.5 0 0 0-3.5 3.5C.5 6 4 10 4 10s3.5-4 3.5-6.5A3.5 3.5 0 0 0 4 0zm0 5a1.4 1.4 0 1 1 0-2.8A1.4 1.4 0 0 1 4 5z" fill="#f6a623"/></svg>18 Kestrel Lane, Harbourview NSW 2061</li>
      <li><svg width="9" height="9" viewBox="0 0 9 9"><path d="M2 0l2 2-1 1.5a6 6 0 0 0 2.5 2.5L7 5l2 2-1.5 2C4 9 0 5 0 1.5z" fill="#f6a623"/></svg>02 5550 1427</li>
      <li><svg width="10" height="8" viewBox="0 0 10 8"><rect width="10" height="8" fill="#f6a623"/><path d="M0 0l5 4 5-4" fill="none" stroke="#1f1f1f"/></svg>hello@brightwattlejourneys.com.au</li>
    </ul>
  </div>
  <div class="foot-brand"><div class="brand-mark"></div><span>Bright Wattle Journeys</span></div>
</footer>
<div class="bottom">© 2015 Bright Wattle Journeys. All rights reserved.</div>

</body>
</html>
```